NEW Modern Sleek Business Card for VR Language Startup

Our startup is using VR to lead the next wave of world language education. We need a two-sided business card that introduces the larger organization (Brightloom Language Inc) and our contact info on one side and shows the product, Glimwoorld, on the other side.

Side 1 (contact info)= Brightloom Logo and Contact info (name, title, phone, email)

Side 2 (product)= Glimworld logo, text, and website
Text= Culturally Immersive Language Learning Games
Website= www.glimworld-play.com

Target Market(s)

Education, Technology

Contact Information for Business Card

Contact info will be updated upon approval of the design. For now, put this as a placeholder.

Perry Dunmore
Founder & CEO
pdunmore@quillpost-mail.net
(555)-014-2286

Font styles to use
Other font styles liked:
• Gibson and Century Gothic are the brand fonts

Requirements
Nice to have
• I would love to see cohesion between the design and colors of the two logos. I have attached a few business card designs that I like, so you can get a feel for my preferred style.

```html
<!DOCTYPE html>
<html lang="en">
<head>
<meta charset="utf-8">
<title>Brightloom Language Inc — Business Card</title>
<link href="https://fonts.googleapis.com/css2?family=Montserrat:wght@500;700&family=Questrial&display=swap" rel="stylesheet">
<style>
  :root {
    --stage: #8a8a8e;
    --card-dark: #070808;
    --card-light: #2b2b2c;
    --cyan: #22d8ee;
    --blue: #3f8cf2;
    --violet: #7a55f3;
    --white: #f4f4f6;
    --grey-text: #6a6a6c;
    --rule: #2b6fd6;
  }
  * { box-sizing: border-box; margin: 0; padding: 0; }
  html, body { width: 1200px; height: 1200px; overflow: hidden; }
  body {
    background: var(--stage);
    font-family: "Questrial", "Century Gothic", sans-serif;
    position: relative;
  }
  .card {
    position: absolute;
    left: 100px;
    width: 1000px;
    height: 560px;
    border-radius: 36px;
    background: linear-gradient(125deg, var(--card-dark) 0%, #141515 45%, var(--card-light) 100%);
    box-shadow: 0 18px 40px rgba(0,0,0,.35);
    overflow: hidden;
  }
  .card--product { top: 25px; }
  .card--contact { top: 615px; }

  /* Product side */
  .product-brand {
    position: absolute;
    top: 150px; left: 0; right: 0;
    display: flex; align-items: center; justify-content: center; gap: 22px;
  }
  .brand-dot {
    width: 74px; height: 74px; border-radius: 50%;
    background: var(--blue);
  }
  .product-name {
    font-family: "Questrial", "Century Gothic", sans-serif;
    font-size: 92px;
    color: var(--blue);
    letter-spacing: 1px;
  }
  .product-tagline {
    position: absolute;
    top: 290px; left: 0; right: 0;
    text-align: center;
    font-size: 27px;
    color: var(--blue);
    letter-spacing: 1px;
  }
  .product-web {
    position: absolute;
    top: 390px; left: 0; right: 0;
    text-align: center;
    font-family: "Montserrat", sans-serif;
    font-weight: 700;
    font-size: 22px;
    color: var(--blue);
    letter-spacing: 1px;
  }

  /* Contact side */
  .company-brand {
    position: absolute;
    top: 240px; left: 110px; width: 370px;
    display: flex; align-items: center; gap: 16px;
  }
  .company-brand .brand-dot { width: 46px; height: 46px; background: var(--violet); }
  .company-name {
    font-family: "Montserrat", sans-serif;
    font-weight: 700;
    font-size: 40px;
    letter-spacing: 4px;
    color: var(--white);
    text-transform: uppercase;
  }
  .divider {
    position: absolute;
    left: 510px; top: 170px;
    width: 2px; height: 210px;
    background: var(--rule);
  }
  .contact {
    position: absolute;
    left: 548px; top: 178px;
  }
  .contact-name {
    font-family: "Montserrat", sans-serif;
    font-weight: 700;
    font-size: 36px;
    color: var(--violet);
    letter-spacing: 1px;
    text-transform: uppercase;
  }
  .contact-title {
    font-size: 24px;
    color: var(--white);
    margin-top: 2px;
  }
  .contact-list { list-style: none; margin-top: 34px; }
  .contact-item {
    display: flex; align-items: center; gap: 14px;
    font-size: 24px;
    color: var(--white);
    margin-bottom: 10px;
  }
  .contact-icon { width: 22px; height: 22px; flex: none; }
</style>
</head>
<body>

  <section class="card card--product" aria-label="Product side">
    <div class="product-brand">
      <span class="brand-dot"></span>
      <span class="product-name">Glimworld</span>
    </div>
    <p class="product-tagline">Culturally Immersive Language Learning Games</p>
    <p class="product-web">www.glimworld-play.com</p>
  </section>

  <section class="card card--contact" aria-label="Contact side">
    <div class="company-brand">
      <span class="brand-dot"></span>
      <span class="company-name">Brightloom</span>
    </div>
    <div class="divider"></div>
    <div class="contact">
      <h1 class="contact-name">Perry Dunmore</h1>
      <p class="contact-title">President</p>
      <ul class="contact-list">
        <li class="contact-item">
          <svg class="contact-icon" viewBox="0 0 24 24" fill="none" stroke="#22d8ee" stroke-width="2">
            <rect x="2" y="5" width="20" height="14" rx="1"/>
            <path d="M2 6l10 7 10-7"/>
          </svg>
          <span>pdunmore@quillpost-mail.net</span>
        </li>
        <li class="contact-item">
          <svg class="contact-icon" viewBox="0 0 24 24" fill="none" stroke="#22d8ee" stroke-width="1.8">
            <circle cx="12" cy="12" r="10"/>
            <ellipse cx="12" cy="12" rx="4.5" ry="10"/>
            <path d="M2 12h20M4 7h16M4 17h16"/>
          </svg>
          <span>(555)-014-2286</span>
        </li>
      </ul>
    </div>
  </section>

</body>
</html>
```